Very new and innovative Web design for Property managers of Vacation rentals

We are looking for a new website design for travel agencies and property managers specialised on vacation rentals business, holiday villas and apartments.

The end users of this website are travellers who are looking for a vacation home for their next holiday: this is the reason why the website must be easy to use, attractive, professional, possibly elegant and focused on get new reservations.

This is a draft of our current website: https://intro3.kelumsito.com/
Please consider that we would like to have proposals with a totally different and innovative layout, surprise us!

These are the pages of the website:
• Homepage: feel free to redesign all the homepage as you wish, surprise us with something very new! Please consider that Property manager/Travel agencies usually want to have the opportunity to put in evidence groups of houses with specific characteristics (eg. villas with private swimming pool, apartment in big/small towns, villas with air co, etc…), destinations and tourist areas, and sometimes experiences or activities (please consider that the website layout must be suitable even if some of the previous sections are not used).
• Search page: we’d like to organise the results of the search page in three different ways:
o Grid
o Map
o List
• Property page: to illustrate the characteristics, descriptions, images, …. of the property. It is very important to put in evidence images of the property and to maintain the booking form (and the other call to action bottom – eg. whatsapp) always visible
• Custom pages: static pages composed usually by text, images and call to actions
• Contact us (general form)
• Info request (specific of a property form)
• Booking process
• Blog, organised in four pages:
o Home Page – introduction to the blog
o List of articles
o Single article
o Site Map (presentation of categories and sub-categories)

If possible, we’d prefer to receive the material in Adobe XD or similar so that we can obtain the three versions:
- smartphone
- tablet
- desktop

The website will be then developed in Bootstrap: as a result we’ll need the icons in SVG format (or the library used)

In attachment you can find the map of the website pages

```html
<!DOCTYPE html>
<html lang="en">
<head>
<meta charset="utf-8">
<title>Casavia – Exclusive Villas in Italy</title>
<link href="https://fonts.googleapis.com/css2?family=Playfair+Display:wght@400;700&family=Lato:wght@400;700&display=swap" rel="stylesheet">
<style>
:root{
  --green:#00b67a;
  --green-dark:#009c68;
  --ink:#222;
  --text:#444;
  --muted:#8a8f8e;
  --dark:#1f2826;
  --footer:#232323;
  --soft:#f2f4f3;
  --line:#d9dcdb;
  --white:#fff;
}
*{box-sizing:border-box;margin:0;padding:0}
html,body{width:1200px;height:5275px;overflow:hidden}
body{position:relative;background:var(--white);font-family:"Lato",sans-serif;color:var(--text)}
.abs{position:absolute}
.photo{position:absolute}
.btn{position:absolute;background:var(--green);color:var(--white);font:700 11px "Lato",sans-serif;letter-spacing:.5px;display:flex;align-items:center;justify-content:center;text-transform:uppercase}
.section-title{position:absolute;left:0;width:1200px;text-align:center;font:700 40px "Playfair Display",serif;color:var(--ink)}
/* header */
.site-header{position:absolute;left:0;top:0;width:1200px;height:92px;background:var(--white)}
.brand{position:absolute;left:112px;top:32px;display:flex;align-items:center;gap:10px;font:400 28px "Lato",sans-serif;color:var(--green)}
.brand-mark{width:30px;height:30px;border-radius:50%;background:var(--green)}
.top-tab{position:absolute;left:809px;top:0;width:391px;height:37px}
.top-tab-links{position:absolute;right:105px;top:12px;display:flex;gap:26px;color:var(--white);font:700 11px "Lato",sans-serif;text-transform:uppercase}
.top-tab-links span{display:flex;align-items:center;gap:5px}
.main-nav{position:absolute;top:61px;left:568px;font:400 12.5px "Lato",sans-serif;text-transform:uppercase;color:#333}
.main-nav a{position:absolute;white-space:nowrap;text-decoration:none;color:#333}
.main-nav a.active{color:var(--green);font-weight:700}
/* hero */
.hero{position:absolute;left:0;top:92px;width:1200px;height:516px;background:linear-gradient(100deg,#1d2a2c 0%,#2f4a4e 30%,#54705f 55%,#8c6d4a 75%,#3e5a34 100%)}
.hero-kicker{position:absolute;left:112px;top:318px;font:400 36px "Playfair Display",serif;color:var(--white)}
.hero-title{position:absolute;left:112px;top:356px;font:700 62px "Playfair Display",serif;color:var(--white)}
.hero-text{position:absolute;left:112px;top:432px;width:440px;font:400 13px/22px "Lato",sans-serif;color:var(--white)}
.search-box{position:absolute;left:112px;top:557px;width:976px;height:98px;background:var(--white);box-shadow:0 4px 18px rgba(0,0,0,.08)}
.field{position:absolute;top:31px;height:40px;border:1px solid var(--line);font:400 11px "Lato",sans-serif;color:#777;padding:0 12px;display:flex;align-items:center;justify-content:space-between}
.soft{position:absolute;left:0;width:1200px;background:var(--soft)}
.sub{position:absolute;left:0;width:1200px;text-align:center;font:400 13px "Lato",sans-serif;color:#333}
.caption{position:absolute;text-align:center;font:400 19px "Playfair Display",serif;color:#333}
/* holiday */
.holiday-band{position:absolute;left:0;top:1274px;width:1003px;height:653px;background:var(--dark)}
.holiday-accent{position:absolute;left:1003px;top:1274px;width:197px;height:653px;background:var(--green)}
.holiday-kicker{position:absolute;left:112px;top:1366px;font:400 16px "Playfair Display",serif;color:var(--white)}
.holiday-title{position:absolute;left:112px;top:1384px;font:700 38px "Playfair Display",serif;color:var(--white)}
.holiday-text{position:absolute;left:112px;top:1442px;width:835px;font:400 12.5px/24px "Lato",sans-serif;color:#c8cdcb}
.card-title{position:absolute;font:400 19px "Playfair Display",serif;color:#222}
.card-text{position:absolute;width:308px;font:400 11.5px/19px "Lato",sans-serif;color:var(--muted)}
.rental-kicker{position:absolute;left:0;width:1200px;text-align:center;font:400 20px "Playfair Display",serif;color:#333}
.rental-name{position:absolute;left:618px;top:3330px;font:700 21px "Playfair Display",serif;color:var(--white)}
.rental-spec{position:absolute;left:618px;font:400 13px "Lato",sans-serif;color:#e5e5e5;width:120px}
.rental-spec b{position:absolute;left:105px;font-weight:400}
.exp-heading{position:absolute;right:665px;text-align:right;font-family:"Playfair Display",serif;color:#222}
.exp-divider{position:absolute;left:600px;top:3553px;width:1px;height:103px;background:var(--line)}
.exp-intro{position:absolute;left:670px;top:3580px;width:400px;font:400 13px/20px "Lato",sans-serif;color:#666}
.feature-icon{position:absolute;width:68px;height:68px;border-radius:50%;background:var(--green);display:flex;align-items:center;justify-content:center}
.feature-title{position:absolute;font:400 19px "Playfair Display",serif;color:#222}
.feature-text{position:absolute;width:340px;font:400 11.5px/18px "Lato",sans-serif;color:var(--muted)}
.blog-title{position:absolute;width:310px;font:400 19px/28px "Playfair Display",serif;color:#222}
.input{position:absolute;height:37px;border:1px solid var(--line);background:var(--white);font:400 11px "Lato",sans-serif;color:#777;padding:0 14px;display:flex;align-items:center}
/* footer */
.site-footer{position:absolute;left:0;top:4952px;width:1200px;height:323px;background:var(--footer)}
.footer-brand{position:absolute;left:112px;top:128px;display:flex;align-items:center;gap:10px;font:400 26px "Lato",sans-serif;color:var(--green)}
.footer-brand .brand-mark{width:28px;height:28px}
.footer-col{position:absolute;top:56px}
.footer-col h4{font:400 17px "Playfair Display",serif;color:var(--white);margin-bottom:16px}
.footer-col li{list-style:none;font:400 12px "Lato",sans-serif;color:#a9adac;height:28px}
.contact-line{display:flex;gap:8px;font:400 12px/17px "Lato",sans-serif;color:#a9adac;margin-bottom:18px}
.social{display:flex;align-items:center;gap:10px;font:400 12px "Lato",sans-serif;color:#a9adac;height:35px}
.social i{width:26px;height:26px;border-radius:50%;background:var(--white);display:block}
.copyright{position:absolute;left:0;top:255px;width:1200px;text-align:center;font:400 11.5px "Lato",sans-serif;color:#a9adac}
.copyright b{color:var(--white);font-weight:700}
</style>
</head>
<body>

<header class="site-header">
  <div class="brand"><span class="brand-mark"></span>Casavia</div>
  <svg class="top-tab" viewBox="0 0 391 37"><polygon points="0,0 391,0 391,37 36,37" fill="#00b67a"/></svg>
  <div class="top-tab-links">
    <span><svg width="11" height="11" viewBox="0 0 12 12"><circle cx="6" cy="4" r="2.6" fill="none" stroke="#fff" stroke-width="1.3"/><path d="M1.5 11.5c0-2.6 2-4 4.5-4s4.5 1.4 4.5 4" fill="none" stroke="#fff" stroke-width="1.3"/></svg>Login</span>
    <span><svg width="12" height="11" viewBox="0 0 12 11"><path d="M6 10 1.3 5.3a2.6 2.6 0 0 1 3.7-3.7L6 2.6l1-1a2.6 2.6 0 0 1 3.7 3.7z" fill="none" stroke="#fff" stroke-width="1.2"/></svg>Wishlist</span>
    <span>EN &#709;</span>
  </div>
  <nav class="main-nav">
    <a class="active" style="left:0">Home</a>
    <a style="left:96px">Search</a>
    <a style="left:203px">Property</a>
    <a style="left:324px">Custom</a>
    <a style="left:437px">Contact Us</a>
  </nav>
  <div class="abs" style="left:568px;top:84px;width:42px;height:2px;background:var(--green)"></div>
</header>

<section>
  <div class="hero" role="img" aria-label="Photo of an Italian lakeside village with a church spire and mountains"></div>
  <div class="hero-kicker">Exclusive</div>
  <h1 class="hero-title">Villas in Italy</h1>
  <p class="hero-text">Our vacation homes are all located in Italy and we take care of them and their owners at every time.</p>
</section>

<div class="soft" style="top:608px;height:590px"></div>
<form class="search-box">
  <div class="field" style="left:23px;width:232px">Destination: <svg width="9" height="12" viewBox="0 0 9 12"><path d="M4.5 11.5S1 7 1 4.5a3.5 3.5 0 0 1 7 0C8 7 4.5 11.5 4.5 11.5z" fill="#888"/><circle cx="4.5" cy="4.5" r="1.3" fill="#fff"/></svg></div>
  <div class="field" style="left:266px;width:166px">Check In <svg width="11" height="11" viewBox="0 0 11 11"><rect x="1" y="2" width="9" height="8" fill="#888"/><rect x="2" y="4" width="7" height="5" fill="#fff"/></svg></div>
  <div class="field" style="left:441px;width:166px">Check Out <svg width="11" height="11" viewBox="0 0 11 11"><rect x="1" y="2" width="9" height="8" fill="#888"/><rect x="2" y="4" width="7" height="5" fill="#fff"/></svg></div>
  <div class="field" style="left:616px;width:166px">Travelers <span>&#709;</span></div>
  <div class="btn" style="left:789px;top:31px;width:166px;height:40px">Search</div>
</form>

<section>
  <h2 class="section-title" style="top:717px">Best Opportunity</h2>
  <p class="sub" style="top:776px">To put in Evidence groups of Houses with Specific Characteristics</p>
  <div class="photo" style="left:112px;top:821px;width:308px;height:266px;background:linear-gradient(135deg,#e9c36b,#c9a77a 50%,#5fb7c6)" role="img" aria-label="Woman relaxing at a private swimming pool"></div>
  <div class="photo" style="left:446px;top:821px;width:308px;height:266px;background:linear-gradient(160deg,#7aa8d6,#b98a5e 50%,#3d5d70)" role="img" aria-label="Canal lined with old town buildings"></div>
  <div class="photo" style="left:780px;top:821px;width:308px;height:266px;background:linear-gradient(170deg,#8fa4b4,#5b6a70 45%,#2f2c2a)" role="img" aria-label="Bedroom with large window overlooking a bay"></div>
  <div class="caption" style="left:112px;top:1100px;width:308px">Private Swimming Pool</div>
  <div class="caption" style="left:446px;top:1100px;width:308px">Apartment in Big/Small Towns</div>
  <div class="caption" style="left:780px;top:1100px;width:308px">Villas with Air Conditions</div>
</section>

<section>
  <div class="holiday-band"></div>
  <div class="holiday-accent"></div>
  <div class="holiday-kicker">Looking for an</div>
  <h2 class="holiday-title">Exclusive Holiday?</h2>
  <p class="holiday-text">Browse our vacation rental selections if you are looking for a real experiences, our portal is the right solution.<br>Our vacation homes are all located in Italy and we take care of them and their owners at every time. Our goal is give to our guest authentic taste of holiday and our country. Our team is always ready to assure the best time and take care of you! Add a local experience to your stay with us: by diving into our local "network" you can have the unique chance to discover and travel our culture through the eye of a local..!</p>
  <div class="photo" style="left:112px;top:1583px;width:976px;height:440px;background:linear-gradient(100deg,#b9ae96 0%,#8b8a74 30%,#4f9ac4 50%,#6fb6dc 80%,#9ccbe6 100%)" role="img" aria-label="Clifftop sanctuary above a blue sea with boats"></div>
</section>

<section>
  <h2 class="section-title" style="top:2084px">Destinations &amp; Tourist Areas</h2>

  <div class="photo" style="left:112px;top:2158px;width:308px;height:265px;background:linear-gradient(180deg,#9ec6e6,#c69a6a 45%,#8b6a48)" role="img" aria-label="Roman Colosseum"></div>
  <div class="photo" style="left:446px;top:2158px;width:308px;height:265px;background:linear-gradient(180deg,#9fcbe8,#c47b55 40%,#3f8f86)" role="img" aria-label="Grand Canal with boats"></div>
  <div class="photo" style="left:780px;top:2158px;width:308px;height:265px;background:linear-gradient(180deg,#bcd6e5,#a99684 55%,#6e8e97)" role="img" aria-label="Venice skyline across the lagoon"></div>
  <div class="card-title" style="left:112px;top:2436px">Roman Coliseum</div>
  <div class="card-title" style="left:446px;top:2436px">Canal of a City</div>
  <div class="card-title" style="left:780px;top:2436px">Venice Italy</div>
  <p class="card-text" style="left:112px;top:2472px">If you use this site regularly and would like to help keep the site on the Internet</p>
  <p class="card-text" style="left:446px;top:2472px">If you use this site regularly and would like to help keep the site on the Internet</p>
  <p class="card-text" style="left:780px;top:2472px">If you use this site regularly and would like to help keep the site on the Internet</p>
  <div class="btn" style="left:112px;top:2523px;width:105px;height:39px">View More</div>
  <div class="btn" style="left:446px;top:2523px;width:105px;height:39px">View More</div>
  <div class="btn" style="left:780px;top:2523px;width:105px;height:39px">View More</div>

  <div class="photo" style="left:112px;top:2599px;width:308px;height:264px;background:linear-gradient(160deg,#b07a5a,#8c5c44 50%,#5e3d2f)" role="img" aria-label="Rock-cut facade at Petra"></div>
  <div class="photo" style="left:446px;top:2599px;width:308px;height:264px;background:linear-gradient(180deg,#3f86d8,#8cc0ec 45%,#e6e3dc 70%,#5f8f4a)" role="img" aria-label="Leaning Tower of Pisa"></div>
  <div class="photo" style="left:780px;top:2599px;width:308px;height:264px;background:linear-gradient(180deg,#142a58,#2a3f78 45%,#c99a4a 75%,#3a2a1a)" role="img" aria-label="Vatican basilica lit at dusk"></div>
  <div class="card-title" style="left:112px;top:2876px">Petra Uum in Jordan</div>
  <div class="card-title" style="left:446px;top:2876px">Tower of Pisa</div>
  <div class="card-title" style="left:780px;top:2876px">Vatican Building at Dusk</div>
  <p class="card-text" style="left:112px;top:2912px">If you use this site regularly and would like to help keep the site on the Internet</p>
  <p class="card-text" style="left:446px;top:2912px">If you use this site regularly and would like to help keep the site on the Internet</p>
  <p class="card-text" style="left:780px;top:2912px">If you use this site regularly and would like to help keep the site on the Internet</p>
  <div class="btn" style="left:112px;top:2963px;width:105px;height:39px">View More</div>
  <div class="btn" style="left:446px;top:2963px;width:105px;height:39px">View More</div>
  <div class="btn" style="left:780px;top:2963px;width:105px;height:39px">View More</div>
</section>

<section>
  <div class="soft" style="top:3082px;height:117px"></div>
  <div class="rental-kicker" style="top:3107px">New Villas &amp;</div>
  <h2 class="section-title" style="top:3130px">Vacation Rentals</h2>
  <div class="photo" style="left:0;top:3199px;width:300px;height:283px;background:linear-gradient(180deg,#8fbbe0,#d9d4c9 45%,#1f9fd2)" role="img" aria-label="Modern villa with infinity pool"></div>
  <div class="photo" style="left:300px;top:3199px;width:300px;height:283px;background:linear-gradient(180deg,#3d8fd8,#e0d4bc 50%,#2ba6d4)" role="img" aria-label="Stone villa with swimming pool"></div>
  <div class="photo" style="left:600px;top:3199px;width:300px;height:283px;background:linear-gradient(180deg,#4a4a48,#2a2c2b)" role="img" aria-label="Podere Il Lauro villa exterior"></div>
  <div class="photo" style="left:900px;top:3199px;width:300px;height:283px;background:linear-gradient(180deg,#d89a5a,#c77a58 45%,#3aa8c8)" role="img" aria-label="Woman in a pool at a villa"></div>
  <div class="rental-name">Podere Il Lauro</div>
  <div class="rental-spec" style="top:3371px">Sleeps<b>27</b></div>
  <div class="rental-spec" style="top:3393px">Bedrooms<b>10</b></div>
  <div class="btn" style="left:618px;top:3426px;width:105px;height:37px">View Details</div>
</section>

<section>
  <div class="exp-heading" style="top:3552px;font-size:22px">sometimes</div>
  <div class="exp-heading" style="top:3578px;font-size:40px;font-weight:700">Experiences or</div>
  <div class="exp-heading" style="top:3622px;font-size:40px;font-weight:700">Activities</div>
  <div class="exp-divider"></div>
  <p class="exp-intro">Consectetur adipiscing elit, sed do eiusmod tempor incididunt ut labore ausmod tempor incididunt ut labore et dolore. Proin eget tellus tristique lacinia erat non.</p>

  <div class="feature-icon" style="left:112px;top:3720px"><svg width="30" height="30" viewBox="0 0 30 30"><path d="M4 13 15 5l11 8v13H4z" fill="#fff"/><rect x="9" y="15" width="4" height="4" fill="#00b67a"/><rect x="17" y="15" width="4" height="4" fill="#00b67a"/><rect x="13" y="20" width="4" height="6" fill="#00b67a"/></svg></div>
  <div class="feature-title" style="left:194px;top:3710px">Luxury Villas</div>
  <p class="feature-text" style="left:194px;top:3741px">This selection of properties includes all the best rentals available. Most with private swimming pool with chef and maid services available.</p>

  <div class="feature-icon" style="left:670px;top:3720px"><svg width="30" height="30" viewBox="0 0 30 30"><circle cx="13" cy="13" r="7" fill="none" stroke="#fff" stroke-width="3"/><path d="M18 18l7 7" stroke="#fff" stroke-width="3.5" stroke-linecap="round"/></svg></div>
  <div class="feature-title" style="left:752px;top:3710px">Browse All Vacation Rentals</div>
  <p class="feature-text" style="left:752px;top:3741px">From here you can browse all the villa selections, you can refine them by using the filters on the search results web page.</p>

  <div class="feature-icon" style="left:112px;top:3840px"><svg width="32" height="30" viewBox="0 0 32 30"><circle cx="16" cy="9" r="4" fill="#fff"/><circle cx="7" cy="12" r="3" fill="#fff"/><circle cx="25" cy="12" r="3" fill="#fff"/><path d="M9 25c0-5 3-8 7-8s7 3 7 8z" fill="#fff"/><path d="M2 25c0-4 2-7 5-7s4 2 4 2M30 25c0-4-2-7-5-7s-4 2-4 2" fill="#fff"/></svg></div>
  <div class="feature-title" style="left:194px;top:3834px">Experiences</div>
  <p class="feature-text" style="left:194px;top:3865px">Don't live just a holiday but an experience! Let's discover our services</p>

  <div class="feature-icon" style="left:670px;top:3840px"><svg width="30" height="30" viewBox="0 0 30 30"><path d="M5 5h10l11 11-10 10L5 15z" fill="#fff"/><circle cx="10" cy="10" r="2" fill="#00b67a"/></svg></div>
  <div class="feature-title" style="left:752px;top:3834px">Last Minute Deals</div>
  <p class="feature-text" style="left:752px;top:3865px">Browse all the last minute deals to browse the villas offering discounts for last minute arrivals.<br>Save money by checking these offers.</p>
</section>

<section>
  <div class="soft" style="top:4004px;height:491px"></div>
  <h2 class="section-title" style="top:4035px">Recent Blog</h2>
  <div class="photo" style="left:112px;top:4110px;width:308px;height:220px;background:linear-gradient(135deg,#7a3a2a,#c9a07a 50%,#e8e2d8)" role="img" aria-label="Hotel receptionist handing a key to a guest"></div>
  <div class="photo" style="left:446px;top:4110px;width:308px;height:220px;background:linear-gradient(135deg,#d9b889,#f1ebe1 50%,#b7906a)" role="img" aria-label="Restaurant table set with plates and glasses"></div>
  <div class="photo" style="left:780px;top:4110px;width:308px;height:220px;background:linear-gradient(180deg,#6fa9e0,#d6d8d4 50%,#3d7aa8)" role="img" aria-label="Seaside resort buildings by a marina"></div>
  <div class="blog-title" style="left:112px;top:4343px">Quis autem vel eum iure reprehenderit qui in ea voluptate</div>
  <div class="blog-title" style="left:446px;top:4343px">Quis autem vel eum iure reprehenderit qui in ea voluptate</div>
  <div class="blog-title" style="left:780px;top:4343px">Quis autem vel eum iure reprehenderit qui in ea voluptate</div>
  <div class="btn" style="left:112px;top:4415px;width:105px;height:37px">Read More</div>
  <div class="btn" style="left:446px;top:4415px;width:105px;height:37px">Read More</div>
  <div class="btn" style="left:780px;top:4415px;width:105px;height:37px">Read More</div>
</section>

<section>
  <h2 class="section-title" style="top:4570px">Quick Contact</h2>
  <div class="input" style="left:262px;top:4645px;width:219px">Name:</div>
  <div class="input" style="left:491px;top:4645px;width:219px">Email:</div>
  <div class="input" style="left:721px;top:4645px;width:217px">Phone:</div>
  <div class="input" style="left:262px;top:4696px;width:676px;height:127px;align-items:flex-start;padding-top:14px">Message</div>
  <div class="btn" style="left:835px;top:4835px;width:103px;height:39px">Submit</div>
</section>

<footer class="site-footer">
  <div class="footer-brand"><span class="brand-mark"></span>Casavia</div>
  <div class="footer-col" style="left:336px">
    <h4>Quick Links</h4>
    <ul><li>Home</li><li>Search</li><li>Property</li><li>Custom</li><li>Contact Us</li></ul>
  </div>
  <div class="footer-col" style="left:526px">
    <h4>Company</h4>
    <ul><li>Privacy Policies</li><li>Reservation Policies</li><li>Cookie Policy</li></ul>
  </div>
  <div class="footer-col" style="left:727px;width:220px">
    <h4>Contact Us</h4>
    <div class="contact-line"><svg width="10" height="13" viewBox="0 0 9 12"><path d="M4.5 11.5S1 7 1 4.5a3.5 3.5 0 0 1 7 0C8 7 4.5 11.5 4.5 11.5z" fill="#fff"/></svg><span>Via dei Colli 24 50014<br>Fiesole, Firenze (Italy)</span></div>
    <div class="contact-line" style="margin-top:20px"><svg width="11" height="11" viewBox="0 0 12 12"><path d="M2 1h3l1 3-2 1a7 7 0 0 0 3 3l1-2 3 1v3c0 1-1 1-1 1C5 11 1 7 1 2c0 0 0-1 1-1z" fill="#fff"/></svg><span>+39 055 4821907</span></div>
    <div class="contact-line" style="margin-top:26px"><svg width="12" height="10" viewBox="0 0 12 10"><rect x=".5" y=".5" width="11" height="9" fill="#fff"/><path d="M1 1l5 4 5-4" fill="none" stroke="#232323"/></svg><span>info@casavia.com</span></div>
  </div>
  <div class="footer-col" style="left:993px">
    <h4>Follow Us</h4>
    <div class="social"><i></i>Friendora</div>
    <div class="social"><i></i>Chirply</div>
    <div class="social"><i></i>Snapfolio</div>
  </div>
  <p class="copyright">Copyright © 2021 <b>Casavia</b>. All rights reserved.</p>
</footer>

</body>
</html>
```